Website Design for Employee Moral and Happiness Company

Looking for a clean website design that explains our features in a step by step manner so our visitors know exactly what our site does before logging in.

The site is called "Velrato". See logo design and video for a sample of style and an overview of what we do.

Target Market(s)

Business owners that are looking to retain employees.

Number of Pages Required

1 page

```html
<!DOCTYPE html>
<html lang="en">
<head>
<meta charset="utf-8">
<title>Velrato – Employee appreciation event planner</title>
<link rel="stylesheet" href="https://fonts.googleapis.com/css2?family=Crimson+Text:wght@600;700&family=Josefin+Sans:ital,wght@0,400;0,600;1,400&display=swap">
<style>
  :root{
    --header-bg:#e8dfd4;
    --page-bg:#e4dbc9;
    --wedge:#cbbfaa;
    --accent:#ff6600;
    --ink:#1a1a1a;
    --heading:#555250;
    --body-text:#4c4a48;
    --nav-text:#3a3a3a;
    --dot-line:#6e6a66;
    --dot-fill:#f1ebe1;
    --panel:#efe9de;
    --panel-shade:#d9d1c1;
  }
  *{box-sizing:border-box;margin:0;padding:0}
  html,body{width:1200px;height:698px;overflow:hidden}
  body{position:relative;background:var(--page-bg);font-family:"Josefin Sans",sans-serif;color:var(--body-text)}
  .backdrop{position:absolute;inset:0}
  .site-header{position:absolute;left:0;top:0;width:1200px;height:89px;background:var(--header-bg);border-bottom:1px solid #eee6dc}
  .brand{position:absolute;left:66px;top:22px;display:flex;align-items:center;gap:8px;font-family:"Crimson Text",serif;font-weight:700;font-size:40px;line-height:1;color:var(--ink);text-decoration:none}
  .brand-dot{width:11px;height:11px;border-radius:50%;background:var(--accent);margin-top:10px}
  .main-nav{position:absolute;left:278px;top:36px;display:flex;gap:23px;font-size:16px}
  .main-nav a{color:var(--nav-text);text-decoration:none}
  .main-nav a.is-current{color:var(--accent);border-bottom:1px solid var(--accent);padding-bottom:1px}
  .login{position:absolute;left:906px;top:36px;display:flex;align-items:center;gap:9px;font-size:16px;color:var(--nav-text);text-decoration:none}
  .btn-signup{position:absolute;left:995px;top:18px;width:140px;height:45px;border-radius:23px;background:var(--accent);color:#fff;font-weight:600;font-size:16px;display:flex;align-items:center;justify-content:center;text-decoration:none;padding-top:3px}
  .intro{position:absolute;left:67px;top:183px;width:360px}
  .intro h1{font-family:"Crimson Text",serif;font-weight:700;font-size:32px;color:var(--heading);line-height:1.2;margin-bottom:14px}
  .intro p{font-size:15.5px;line-height:30px;letter-spacing:.2px}
  .intro p + p{margin-top:30px}
  .btn-cta{position:absolute;left:67px;top:546px;width:245px;height:52px;border-radius:13px 13px 6px 6px;background:var(--accent);color:#fff;font-weight:600;font-size:17px;display:flex;align-items:center;justify-content:center;text-decoration:none;padding-top:3px;word-spacing:4px}
  .planner-visual{position:absolute;left:433px;top:230px;width:640px;height:326px;border-radius:14px;background:linear-gradient(135deg,var(--panel) 0%,var(--panel-shade) 100%)}
  .section-steps{position:absolute;left:1090px;top:260px;width:110px;height:270px}
  .step-label{position:absolute;right:30px;top:78px;font-size:11.5px;font-style:italic;line-height:13px;color:#3a3a3a;text-align:left;width:70px}
</style>
</head>
<body>
  <svg class="backdrop" width="1200" height="698" aria-hidden="true">
    <polygon points="77,89 1153,698 0,698 0,89" fill="var(--wedge)"/>
  </svg>

  <header class="site-header">
    <a class="brand" href="#">velrato<span class="brand-dot"></span></a>
    <nav class="main-nav">
      <a class="is-current" href="#">Home</a>
      <a href="#">Boring Work Events</a>
      <a href="#">Introducing Velrato</a>
      <a href="#">Why Velrato</a>
      <a href="#">Testimonials</a>
    </nav>
    <a class="login" href="#">
      <svg width="12" height="12" viewBox="0 0 12 12" fill="none" stroke="#3a3a3a" stroke-width="1.2"><path d="M1 6h6M5 3.5 7.5 6 5 8.5M8 1h3v10H8"/></svg>
      Login
    </a>
    <a class="btn-signup" href="#">SIGN UP</a>
  </header>

  <section class="intro">
    <h1>Introducing velrato</h1>
    <p>velrato is your all in one event planner for employee appreciation activities, from raffles to auction.</p>
    <p>It provide you with all the tools you need to plan and run your work event, boost your employee morals<br>and transform your boring work events to engaging one.</p>
  </section>
  <a class="btn-cta" href="#">SIGN UP NOW</a>

  <div class="planner-visual" role="img" aria-label="Illustration of an event planner dashboard with contacts, messages, schedule, calendar, email and task panels"></div>

  <nav class="section-steps" aria-label="Sections">
    <svg width="110" height="270" viewBox="0 0 110 270">
      <line x1="85" y1="10" x2="85" y2="258" stroke="var(--dot-line)" stroke-width="1.3"/>
      <g fill="var(--dot-fill)" stroke="var(--dot-line)" stroke-width="1.3">
        <circle cx="85" cy="10" r="6"/>
        <circle cx="85" cy="51" r="6"/>
        <circle cx="85" cy="134" r="6"/>
        <circle cx="85" cy="175" r="6"/>
        <circle cx="85" cy="216" r="6"/>
        <circle cx="85" cy="258" r="6"/>
      </g>
      <circle cx="85" cy="92" r="11" fill="#b9b2a8"/>
      <circle cx="85" cy="92" r="6.5" fill="#2e2e2e"/>
    </svg>
    <span class="step-label">Introducing velrato</span>
  </nav>
</body>
</html>
```